Stage Design Company Business Card

We are looking to step up up our business card design for our team.

We are a Full service Design and Consultation company for Stage and TV with an emphasis in Theatrical Lighting.

We like our materials to be clean and modern with solid colors free of patterns and gradients. Our brand consists of 4 primary colors Purple, Black, Grey, and White. Provided is our Word Mark as well as our Symbol Logo.

We would like our cards to leave an impression beyond the information, show our attention to design and detail, and make our marks an easily recognized feature (together or apart) for our clients.

We need a warm approachable comfortable feel for some clients, and a professional flair for the board member type clients.

Attached are our brand elements, and our existing cards to give a sense of our style and a glipse at the information we provide on our cards.

Target Market(s)

broad client base from church leaders to high school teachers and architects.

Industry/Entity Type

Business

Contact Information for Business Card

We format our phone number with periods not parenthesis or dashes. Information will be edited for each of our team members, and team member specific cards are not part of this scope, but rather a template so to speak.

Font styles to use
Sans Serif

Colors
6b449b
ffffff
000000
333333
aaaaaa

Requirements
Must have
• Wordmark and logo mark present (does not need to exist on the same side of card)
• Brand Colors,
• Name, Phone, Email, Address.
• Unique choices that make someone stop and take a second look
Nice to have
• It would be nice to somehow convey what we DO, as our brand name does not lend itself to this, outside of an obvious tagline though.....
• social media if not crowded. all of our handles match (instagram, twitter, facebook)
Should not have
• "clipart"

```html
<!DOCTYPE html>
<html lang="en">
<head>
<meta charset="utf-8">
<title>Ellison Stageworks – Business Card</title>
<link rel="stylesheet" href="https://fonts.googleapis.com/css2?family=Jost:wght@400;500;700&display=swap">
<style>
  :root {
    --purple: #36226a;
    --purple-brand: #6b449b;
    --white: #ffffff;
    --black: #1a1a1a;
    --charcoal: #333333;
    --grey: #aaaaaa;
    --stage: #8d8c8d;
  }
  * { box-sizing: border-box; margin: 0; padding: 0; }
  html, body { width: 1200px; height: 929px; overflow: hidden; }
  body {
    background: var(--stage);
    font-family: "Jost", "Helvetica Neue", Arial, sans-serif;
    position: relative;
  }
  .card {
    position: absolute;
    width: 510px;
    height: 292px;
    box-shadow: 0 10px 24px rgba(0,0,0,.25);
    overflow: hidden;
  }
  /* Back side */
  .card--back {
    left: 120px; top: 130px;
    background: var(--purple);
    display: flex; flex-direction: column; align-items: center; justify-content: center;
    color: var(--white);
  }
  .brand { display: flex; flex-direction: column; align-items: center; gap: 12px; }
  .brand__dot { width: 64px; height: 64px; border-radius: 50%; border: 3px solid currentColor; }
  .brand__name {
    font-weight: 500; font-size: 26px; letter-spacing: 9px; text-transform: uppercase;
  }
  .card--back .brand__name { font-size: 24px; }

  /* Front side */
  .card--front {
    left: 570px; top: 480px;
    background: var(--white);
  }
  .card--front .brand {
    position: absolute; left: 34px; top: 78px; width: 200px;
    color: var(--purple);
  }
  .card--front .brand__name { font-size: 20px; letter-spacing: 6px; color: var(--purple); }
  .divider {
    position: absolute; left: 250px; top: 42px; width: 1.5px; height: 150px;
    background: var(--purple);
  }
  .contact { position: absolute; left: 272px; top: 38px; color: var(--charcoal); }
  .contact__name { font-weight: 700; font-size: 21px; color: var(--purple); letter-spacing: .5px; line-height: 1.1; }
  .contact__role { font-size: 15px; color: var(--charcoal); margin-bottom: 12px; }
  .contact__address { font-size: 14px; line-height: 1.25; margin-left: 20px; margin-bottom: 10px; }
  .contact__list { list-style: none; font-size: 14px; line-height: 1.35; }
  .contact__list li { display: flex; align-items: center; gap: 8px; }
  .contact__list svg { width: 12px; height: 12px; flex: none; }
  .swoosh { position: absolute; left: 0; bottom: 0; width: 510px; height: 160px; }
</style>
</head>
<body>
  <section class="card card--back" aria-label="Card back">
    <div class="brand">
      <span class="brand__dot"></span>
      <span class="brand__name">Ellison Stageworks</span>
    </div>
  </section>

  <section class="card card--front" aria-label="Card front">
    <div class="brand">
      <span class="brand__dot"></span>
      <span class="brand__name">Ellison Stageworks</span>
    </div>
    <span class="divider"></span>
    <div class="contact">
      <p class="contact__name">MARK T ELLISON</p>
      <p class="contact__role">Owner</p>
      <p class="contact__address">412 N. Cedar AVE<br>Tempe, AZ 85281</p>
      <ul class="contact__list">
        <li><svg viewBox="0 0 12 12"><rect x="3" y="0.5" width="6" height="11" rx="1" fill="none" stroke="#36226a" stroke-width="1.2"/></svg>800.555.0148</li>
        <li><svg viewBox="0 0 12 12"><rect x="0.5" y="2" width="11" height="8" fill="#36226a"/><path d="M0.5 2 L6 7 L11.5 2" fill="none" stroke="#fff" stroke-width="1"/></svg>hello@ellison-sw.com</li>
        <li><svg viewBox="0 0 12 12"><circle cx="5" cy="5" r="3.6" fill="none" stroke="#36226a" stroke-width="1.6"/><path d="M7.6 7.6 L11 11" stroke="#36226a" stroke-width="1.8"/></svg>ellison-sw.com</li>
      </ul>
    </div>
    <svg class="swoosh" viewBox="0 0 510 160" preserveAspectRatio="none" aria-hidden="true">
      <path d="M510 20 C420 40 330 120 0 150 L0 160 L510 160 Z" fill="#1a1a1a"/>
      <path d="M510 38 C420 60 340 128 0 152 L0 160 L510 160 Z" fill="#36226a"/>
    </svg>
  </section>
</body>
</html>
```